VELQUINT

1. My company will allow people to buy either stock made or custom scented aromatherapy candles, lotions,soaps,body sprays, and wax melts. As there isn't a company that allows for custom oil scent mixes but me. We are just starting with the candles and the other items will be coming later.

2. My target audience is anyone who would want to buy my product. It isn't really limited due to the nature of the product I will be providing.

3. velquint.com is the domain name (purchased from plorvex.com).

4. So what I really need is the shopping cart function. A fully coded shopping cart that will calculate shipping and sales tax if need be. I need the cart function to be just like every other major retailers shopping cart function. So they can click on an item they want and have it go into a shopping cart for the customer to then be able to go and pay for their goods. I also need help creating single pages for each product. So that each thing we make has a separate page with a description and an add to cart button.

5. I would like the color scheme to follow the logo I made. I would also like the logo top center of first page. I would like the quote " elevate your choices in aromatherapy products"

^. I basically need a checkout just like every other good website. A clear shipping area for them to populate, sales tax calculator, ya know everything a normal checkout has like tressly or dunvexa.com. I also have a vonk account already as well.

```html
<!DOCTYPE html>
<html lang="en">
<head>
<meta charset="utf-8">
<title>Velquint — Aromatherapy Products</title>
<link href="https://fonts.googleapis.com/css2?family=Lato:ital,wght@0,400;0,700;0,900;1,400&family=Roboto:wght@400;500;700&display=swap" rel="stylesheet">
<style>
:root{
  --purple:#5b2d91;
  --purple-deep:#3b2586;
  --purple-soft:#7b4bb7;
  --navy:#27306f;
  --blue:#2f7fd0;
  --ink:#1d1d2b;
  --muted:#6b6b78;
  --line:#d9d6e6;
  --white:#ffffff;
  --red:#c62828;
  --tile:#e6e3ec;
}
*{box-sizing:border-box;margin:0;padding:0}
html,body{width:1200px;height:4632px;overflow:hidden}
body{position:relative;background:var(--white);font-family:"Roboto",sans-serif;color:var(--ink)}
.abs{position:absolute}
.ph{position:absolute}
h2.section-title{font-family:"Lato",sans-serif;font-weight:900;font-size:34px;color:var(--navy);letter-spacing:.5px;text-transform:uppercase}

/* top bar */
.topbar{left:0;top:0;width:1200px;height:36px;background:linear-gradient(90deg,#4a2a8a,#6a3bb0 50%,#4a2a8a)}
.topbar p{position:absolute;left:110px;top:10px;font-size:13px;color:var(--white);font-family:"Lato",serif}
.topbar p u{font-weight:700}
.search{position:absolute;left:730px;top:7px;width:190px;height:22px;background:var(--white);border-radius:3px;font-size:11px;color:var(--muted);padding:4px 8px}
.search svg{position:absolute;right:6px;top:5px}

/* nav */
.nav{left:0;top:36px;width:1200px;height:84px;background:var(--white)}
.nav a{position:absolute;top:34px;font-family:"Lato",sans-serif;font-weight:700;font-size:15px;color:var(--ink);text-decoration:none}
.nav a.active{color:var(--purple)}
.nav a.active::after{content:"";position:absolute;left:0;right:0;bottom:-6px;height:2px;background:var(--purple)}
.nav .icons{position:absolute;left:964px;top:32px;display:flex;gap:16px}
.brand{left:520px;top:16px;width:160px;height:160px;border-radius:50%;background:var(--white);border:3px solid var(--purple);display:flex;align-items:center;justify-content:center;z-index:5}
.brand span{font-family:"Lato",sans-serif;font-weight:900;font-size:24px;color:var(--purple);letter-spacing:2px}

/* hero */
.hero{left:0;top:120px;width:1200px;height:560px;background:linear-gradient(120deg,#d9cfe6 0%,#9b7bc2 40%,#5b3a8c 70%,#2b1c44 100%)}
.hero-badge{left:32px;top:184px;width:480px;height:480px;border-radius:50%;background:var(--purple);border:4px solid var(--white);text-align:center;color:var(--white);padding-top:140px}
.hero-badge h1{font-family:"Lato",sans-serif;font-weight:400;font-size:36px;line-height:46px;text-transform:uppercase;white-space:nowrap}
.hero-badge h1 b{font-weight:900}
.btn{display:inline-block;font-family:"Lato",sans-serif;font-weight:700;font-size:13px;letter-spacing:1px;text-transform:uppercase}
.hero-badge .btn{margin-top:26px;border:2px solid var(--white);padding:10px 18px;background:var(--purple)}

/* categories */
.cat{border-radius:10px;overflow:hidden;color:var(--white);text-align:center;font-family:"Lato",sans-serif}
.cat .label{position:absolute;left:0;right:0;font-weight:900;font-size:20px;letter-spacing:1px}
.cat .soon{position:absolute;left:0;right:0;font-size:10px;letter-spacing:1px}
.cat .btn{position:absolute;left:176px;top:444px;padding:10px 20px;border:2px solid var(--white);background:rgba(0,0,0,.3)}

/* candle products */
.arrows{left:572px;top:1468px;display:flex;gap:18px}
.prod-img{background:var(--tile)}
.prod-name{font-family:"Lato",sans-serif;font-weight:700;font-size:17px;text-transform:uppercase;color:var(--ink)}
.prod-name.hl{color:var(--purple);text-decoration:underline}
.price{font-family:"Roboto",sans-serif;font-size:24px;color:var(--red)}
.price s{color:var(--ink);margin-left:6px}
.fav{width:28px;height:28px;border-radius:50%;background:var(--purple);display:flex;align-items:center;justify-content:center}

/* about */
.about{left:0;top:2000px;width:1200px;height:432px;background:linear-gradient(90deg,#ece6f4 0%,#ffffff 30%,#7a49b8 45%,#4b2a8c 100%)}
.about h2{position:absolute;left:580px;top:108px;font-family:"Lato",sans-serif;font-weight:900;font-size:30px;color:var(--white);letter-spacing:1px}
.about p{position:absolute;left:580px;top:156px;width:470px;font-size:14px;line-height:21px;color:var(--white)}
.about .btn{position:absolute;left:580px;top:320px;padding:10px 14px;border:2px solid var(--white);color:var(--white)}

/* carousel arrows */
.circ{width:40px;height:40px;border-radius:50%;display:flex;align-items:center;justify-content:center}
.circ.light{border:2px solid var(--ink);background:var(--white)}
.circ.dark{background:var(--navy)}

/* testimonials */
.testi{left:0;top:3060px;width:1200px;height:360px;background:linear-gradient(90deg,#4c2a8c 0%,#3b4aa8 55%,#2a8fd6 100%)}
.testi h2{position:absolute;left:220px;top:96px;font-family:"Lato",sans-serif;font-weight:900;font-size:32px;color:var(--white)}
.testi p{position:absolute;left:220px;top:144px;width:440px;font-family:"Lato",sans-serif;font-style:italic;font-size:14px;line-height:20px;color:var(--white)}
.testi .who{position:absolute;left:220px;top:246px;font-family:"Lato",sans-serif;font-weight:900;font-size:24px;color:var(--white)}
.dots{left:228px;top:300px;display:flex;gap:6px}
.dots i{width:10px;height:10px;border-radius:50%;background:#9fb3e8}
.dots i:first-child{background:var(--white)}
.testi-photo{left:720px;top:24px;width:380px;height:312px;background:linear-gradient(135deg,#efe6dc,#bfae9f)}

/* blogs */
.blog{border:1px solid var(--line);border-radius:8px;background:var(--white);overflow:hidden}
.blog .img{height:172px}
.blog h3{margin:24px 16px 6px;font-family:"Lato",sans-serif;font-weight:900;font-size:15px;color:var(--ink)}
.blog p{margin:0 16px;font-size:13px;line-height:18px;color:var(--ink)}
.blog .go{position:absolute;right:8px;bottom:8px;width:26px;height:26px;background:var(--ink);display:flex;align-items:center;justify-content:center}

/* footer */
.footer{left:0;top:4140px;width:1200px;height:492px;background:linear-gradient(180deg,#3d2a8a,#34287c)}
.footer h2{position:absolute;left:0;right:0;top:48px;text-align:center;font-family:"Lato",sans-serif;font-weight:900;font-size:34px;color:var(--white)}
.news{position:absolute;left:460px;top:108px;display:flex}
.news span{width:252px;height:40px;background:var(--white);font-size:13px;color:#9a9aa8;padding:12px}
.news b{width:102px;height:40px;background:var(--purple-deep);border:2px solid var(--white);color:var(--white);font-family:"Lato",sans-serif;font-size:13px;display:flex;align-items:center;justify-content:center}
.foot-brand{position:absolute;left:84px;top:168px;width:236px;height:236px;border-radius:50%;border:2px solid rgba(255,255,255,.5);display:flex;align-items:center;justify-content:center}
.foot-brand span{font-family:"Lato",sans-serif;font-weight:900;font-size:30px;color:var(--white);letter-spacing:2px}
.fcol{position:absolute;top:180px;color:var(--white)}
.fcol h4{font-family:"Lato",sans-serif;font-weight:900;font-size:18px;margin-bottom:12px}
.fcol li{list-style:none;font-size:15px;line-height:24px}
.contact-row{display:flex;gap:12px;margin-bottom:16px}
.contact-row .ic{width:36px;height:36px;border-radius:50%;background:var(--white);display:flex;align-items:center;justify-content:center;flex:none}
.contact-row b{display:block;font-family:"Lato",sans-serif;font-size:14px}
.contact-row span{font-size:14px}
.foot-rule{position:absolute;left:0;top:420px;width:1200px;height:1px;background:rgba(255,255,255,.25)}
.pay{position:absolute;left:112px;top:444px;display:flex;gap:8px}
.pay span{width:46px;height:28px;background:var(--white);border-radius:3px;font-family:"Lato",sans-serif;font-weight:700;font-size:10px;color:var(--navy);display:flex;align-items:center;justify-content:center}
.copy{position:absolute;left:0;right:0;top:452px;text-align:center;font-size:13px;color:var(--white)}
.social{position:absolute;left:1010px;top:440px;display:flex;gap:10px}
.social i{width:32px;height:32px;border-radius:50%;background:var(--white)}
</style>
</head>
<body>

<!-- top bar -->
<div class="abs topbar">
  <p>Free Shipping World Wide For All Orders. <u>Shop Now</u></p>
  <div class="search">Search...
    <svg width="12" height="12" viewBox="0 0 12 12"><circle cx="5" cy="5" r="4" fill="none" stroke="#5b2d91" stroke-width="1.6"/><line x1="8" y1="8" x2="11" y2="11" stroke="#5b2d91" stroke-width="1.6"/></svg>
  </div>
</div>

<!-- navigation -->
<nav class="abs nav">
  <a class="active" style="left:112px">Home</a>
  <a style="left:184px">About Us</a>
  <a style="left:282px">Products</a>
  <a style="left:364px">Testimonials</a>
  <a style="left:756px">Contact Us</a>
  <div class="icons">
    <svg width="18" height="18" viewBox="0 0 18 18" fill="none" stroke="#5b2d91" stroke-width="1.8"><circle cx="9" cy="6" r="3.5"/><path d="M2 17c1-4 4-5 7-5s6 1 7 5"/></svg>
    <svg width="18" height="18" viewBox="0 0 18 18" fill="none" stroke="#5b2d91" stroke-width="1.8"><path d="M9 16S2 11 2 6a3.5 3.5 0 0 1 7-1 3.5 3.5 0 0 1 7 1c0 5-7 10-7 10z"/></svg>
    <svg width="20" height="18" viewBox="0 0 20 18" fill="#5b2d91"><path d="M1 1h3l2 10h10l2-7H5" fill="none" stroke="#5b2d91" stroke-width="1.8"/><circle cx="8" cy="15" r="1.6"/><circle cx="15" cy="15" r="1.6"/></svg>
  </div>
</nav>
<div class="abs brand"><span>VELQUINT</span></div>

<!-- hero -->
<section class="abs hero" role="img" aria-label="Photo of purple aromatherapy candles, oil bottles and lavender on stones"></section>
<div class="abs hero-badge">
  <h1><b>Elevate your</b> choices<br>in aromatherapy<br><b>products</b></h1>
  <span class="btn">Buy Now</span>
</div>

<!-- categories -->
<div class="abs cat" style="left:112px;top:764px;width:464px;height:548px;background:linear-gradient(180deg,#3a2a20,#c9822e 55%,#2a1d18)" role="img" aria-label="Photo of a lit candle in a glass jar">
  <span class="label" style="top:396px">CANDLE</span>
  <span class="btn">View All</span>
</div>
<div class="abs cat" style="left:592px;top:764px;width:240px;height:268px;background:linear-gradient(160deg,#6a4a3a,#cbb9a8 60%,#8a6a55)" role="img" aria-label="Photo of lotion jars">
  <span class="label" style="top:198px;font-size:18px">LOTIONS</span><span class="soon" style="top:222px">ARRIVING SOON</span>
</div>
<div class="abs cat" style="left:844px;top:764px;width:244px;height:268px;background:linear-gradient(160deg,#7a4a2a,#c99a6a 55%,#5a3a2a)" role="img" aria-label="Photo of stacked handmade soap bars">
  <span class="label" style="top:198px;font-size:18px">SOAPS</span><span class="soon" style="top:222px">ARRIVING SOON</span>
</div>
<div class="abs cat" style="left:592px;top:1048px;width:496px;height:264px;background:linear-gradient(90deg,#8a8e92,#d9dadb 50%,#a8aaad)" role="img" aria-label="Photo of a body spray bottle">
  <span class="label" style="top:190px;left:20px;right:auto;font-size:18px">BODY SPRAYS</span><span class="soon" style="top:214px;left:20px;right:auto;text-align:left">ARRIVING SOON</span>
</div>

<!-- aromatherapy candles -->
<h2 class="section-title abs" style="left:112px;top:1468px;font-size:28px">Aromatherapy Candles</h2>
<div class="abs arrows">
  <svg width="28" height="20" viewBox="0 0 28 20" fill="none" stroke="#1d1d2b" stroke-width="2.4"><path d="M26 10H3M10 2 2 10l8 8"/></svg>
  <svg width="28" height="20" viewBox="0 0 28 20" fill="none" stroke="#1d1d2b" stroke-width="2.4"><path d="M2 10h23M18 2l8 8-8 8"/></svg>
</div>
<div class="ph prod-img" style="left:112px;top:1548px;width:244px;height:252px" role="img" aria-label="Photo of three candles in black and gold tins"></div>
<div class="ph" style="left:400px;top:1548px;width:244px;height:252px;background:linear-gradient(160deg,#6a3a8a,#c03a5a 55%,#3a2040)" role="img" aria-label="Photo of lit pillar candles"></div>
<div class="abs" style="left:604px;top:1560px;display:flex;flex-direction:column;gap:6px">
  <span class="fav"><svg width="12" height="12" viewBox="0 0 18 18" fill="#fff"><path d="M9 16S2 11 2 6a3.5 3.5 0 0 1 7-1 3.5 3.5 0 0 1 7 1c0 5-7 10-7 10z"/></svg></span>
  <span class="fav"><svg width="12" height="12" viewBox="0 0 12 12" fill="none" stroke="#fff" stroke-width="1.6"><circle cx="5" cy="5" r="4"/><line x1="8" y1="8" x2="11" y2="11"/></svg></span>
</div>
<div class="abs prod-name" style="left:112px;top:1828px">Candles</div>
<div class="abs price" style="left:112px;top:1856px">$16.00<s>$20.00</s></div>
<div class="abs prod-name hl" style="left:400px;top:1828px">Pillar Candles</div>
<div class="abs price" style="left:400px;top:1856px">$13.00<s>$18.00</s></div>
<div class="ph" style="left:712px;top:1408px;width:488px;height:504px;background:radial-gradient(circle at 30% 45%,#f0b04a 0%,#8a4a1a 25%,#1e1410 60%)" role="img" aria-label="Photo of a hand lighting a white candle"></div>

<!-- about -->
<section class="abs about">
  <div class="ph" style="left:40px;top:0;width:480px;height:432px;background:radial-gradient(circle at 50% 50%,#8a5ad0 0%,#b99ee0 30%,rgba(236,230,244,0) 65%)" role="img" aria-label="Decorative purple and blue emblem"></div>
  <h2>ABOUT VELQUINT</h2>
  <p>Lorem ipsum dolor sit amet, consectetur adipiscing elit, sed sed diam nonummy nibh euismod tincidunt ut laoreet dolore magna aliquam erat volutpat. Ut wisi enim ad minim veniam, quis nostrud exerci tation ullamcorper suscipit lobortis nisl ut aliquip ex ea commodo consequat duis autem vel eum iriure dolor in hendrerit in vulputate velit esse molestie.</p>
  <span class="btn">Read More</span>
</section>

<!-- featured products -->
<h2 class="section-title abs" style="left:0;width:1200px;text-align:center;top:2568px">Our Feature Products</h2>
<div class="abs circ light" style="left:44px;top:2748px"><svg width="12" height="12" viewBox="0 0 12 12" fill="none" stroke="#1d1d2b" stroke-width="2"><path d="M8 1 3 6l5 5"/></svg></div>
<div class="abs circ dark" style="left:1116px;top:2748px"><svg width="12" height="12" viewBox="0 0 12 12" fill="none" stroke="#fff" stroke-width="2"><path d="M4 1l5 5-5 5"/></svg></div>

<div class="ph prod-img" style="left:112px;top:2648px;width:220px;height:228px" role="img" aria-label="Photo of an amber lotion dropper bottle"></div>
<div class="ph" style="left:364px;top:2648px;width:220px;height:228px;background:linear-gradient(160deg,#8a5a3a,#d4b08a 55%,#6a4a30)" role="img" aria-label="Photo of handmade soap bars"></div>
<div class="abs" style="left:548px;top:2660px;display:flex;flex-direction:column;gap:6px">
  <span class="fav"><svg width="12" height="12" viewBox="0 0 18 18" fill="#fff"><path d="M9 16S2 11 2 6a3.5 3.5 0 0 1 7-1 3.5 3.5 0 0 1 7 1c0 5-7 10-7 10z"/></svg></span>
  <span class="fav"><svg width="12" height="12" viewBox="0 0 12 12" fill="none" stroke="#fff" stroke-width="1.6"><circle cx="5" cy="5" r="4"/><line x1="8" y1="8" x2="11" y2="11"/></svg></span>
</div>
<div class="ph prod-img" style="left:616px;top:2648px;width:220px;height:228px" role="img" aria-label="Photo of a jar of wax melts"></div>
<div class="ph prod-img" style="left:868px;top:2648px;width:220px;height:228px" role="img" aria-label="Photo of a pink body spray bottle"></div>

<div class="abs prod-name" style="left:112px;top:2904px">Lotions</div>
<div class="abs price" style="left:112px;top:2932px">$16.00<s>$20.00</s></div>
<div class="abs prod-name hl" style="left:364px;top:2904px">Soaps</div>
<div class="abs price" style="left:364px;top:2932px">$13.00<s>$18.00</s></div>
<div class="abs prod-name" style="left:616px;top:2904px">Wax Melts</div>
<div class="abs price" style="left:616px;top:2932px">$23.00<s>$27.00</s></div>
<div class="abs prod-name" style="left:868px;top:2904px">Body Sprays</div>
<div class="abs price" style="left:868px;top:2932px">$19.00<s>$28.00</s></div>

<!-- testimonials -->
<section class="abs testi">
  <h2>CLIENT TESTIMONIALS</h2>
  <p>"Lorem ipsum dolor sit amet, consectetur adipiscing elit, sed do eiusmod tempor incididunt ut labore et dolore magna aliqua. Quis ipsum suspendisse ultrices gravida. Risus commodo viverra maecenas..."</p>
  <div class="who">- Marla</div>
  <div class="abs dots"><i></i><i></i><i></i></div>
  <div class="ph testi-photo" role="img" aria-label="Photo of a customer relaxing with a candle, in a decorative frame"></div>
</section>

<!-- blogs -->
<h2 class="section-title abs" style="left:0;width:1200px;text-align:center;top:3572px">Our Latest Blogs</h2>
<div class="abs circ light" style="left:44px;top:3788px"><svg width="12" height="12" viewBox="0 0 12 12" fill="none" stroke="#1d1d2b" stroke-width="2"><path d="M8 1 3 6l5 5"/></svg></div>
<div class="abs circ dark" style="left:1116px;top:3788px"><svg width="12" height="12" viewBox="0 0 12 12" fill="none" stroke="#fff" stroke-width="2"><path d="M4 1l5 5-5 5"/></svg></div>

<article class="abs blog" style="left:112px;top:3648px;width:300px;height:352px">
  <div class="img" style="background:linear-gradient(160deg,#5a3020,#d49a5a 55%,#3a2018)" role="img" aria-label="Photo of hands holding a lit candle"></div>
  <h3>LOREM IPSUM DOLOR SIT AMET</h3>
  <p>Lorem ipsum dolor sit amet, consectetur adipiscing elit, sed do eiusmod tempor incididunt ut labore et dolore magna aliqua ut enim.</p>
  <span class="go"><svg width="12" height="12" viewBox="0 0 12 12" fill="none" stroke="#fff" stroke-width="2"><path d="M2 10 10 2M4 2h6v6"/></svg></span>
</article>
<article class="abs blog" style="left:452px;top:3648px;width:300px;height:352px">
  <div class="img" style="background:linear-gradient(160deg,#e8e0d8,#b8a08a 60%,#8a7060)" role="img" aria-label="Photo of a relaxing massage with aromatherapy oils"></div>
  <h3>LOREM IPSUM DOLOR SIT AMET</h3>
  <p>Lorem ipsum dolor sit amet, consectetur adipiscing elit, sed do eiusmod tempor incididunt ut labore et dolore magna aliqua ut enim.</p>
  <span class="go"><svg width="12" height="12" viewBox="0 0 12 12" fill="none" stroke="#fff" stroke-width="2"><path d="M2 10 10 2M4 2h6v6"/></svg></span>
</article>
<article class="abs blog" style="left:792px;top:3648px;width:300px;height:352px">
  <div class="img" style="background:linear-gradient(160deg,#3a4a2a,#c9a070 55%,#6a3a2a)" role="img" aria-label="Photo of soap bars with herbs and flowers"></div>
  <h3>LOREM IPSUM DOLOR SIT AMET</h3>
  <p>Lorem ipsum dolor sit amet, consectetur adipiscing elit, sed do eiusmod tempor incididunt ut labore et dolore magna aliqua ut enim.</p>
  <span class="go"><svg width="12" height="12" viewBox="0 0 12 12" fill="none" stroke="#fff" stroke-width="2"><path d="M2 10 10 2M4 2h6v6"/></svg></span>
</article>

<!-- footer -->
<footer class="abs footer">
  <h2>SUBSCRIBE TO OUR NEWSLETTER</h2>
  <div class="news"><span>Email Address</span><b>SUBSCRIBE</b></div>
  <div class="foot-brand"><span>VELQUINT</span></div>
  <div class="fcol" style="left:396px">
    <h4>QUICK LINKS</h4>
    <ul><li>Home</li><li>About Us</li><li>Products</li><li>Testimonials</li><li>Contact Us</li></ul>
  </div>
  <div class="fcol" style="left:592px">
    <h4>OTHER LINKS</h4>
    <ul><li>Shipping Policy</li><li>Return &amp; Refund Policy</li><li>Terms of Service</li><li>Privacy Policy</li><li>FAQ</li><li>Size Guide</li></ul>
  </div>
  <div class="fcol" style="left:840px">
    <h4>CONTACT US</h4>
    <div class="contact-row"><span class="ic"><svg width="16" height="16" viewBox="0 0 16 16" fill="#3b2586"><path d="M3 1h3l1.5 4-2 1.5a9 9 0 0 0 4 4L11 8.5l4 1.5v3a2 2 0 0 1-2 2A13 13 0 0 1 1 3a2 2 0 0 1 2-2z"/></svg></span><div><b>PHONE NO:</b><span>+(000) 555 0142</span></div></div>
    <div class="contact-row"><span class="ic"><svg width="16" height="14" viewBox="0 0 16 14" fill="none" stroke="#3b2586" stroke-width="1.8"><rect x="1" y="1" width="14" height="12"/><path d="M1 1l7 6 7-6"/></svg></span><div><b>EMAIL:</b><span>Info@velquint.com</span></div></div>
    <div class="contact-row"><span class="ic"><svg width="14" height="18" viewBox="0 0 14 18" fill="#3b2586"><path d="M7 0a7 7 0 0 1 7 7c0 5-7 11-7 11S0 12 0 7a7 7 0 0 1 7-7zm0 4a3 3 0 1 0 0 6 3 3 0 0 0 0-6z"/></svg></span><div><b>LOCATION:</b><span>Lorem ipsum dolor, USA</span></div></div>
  </div>
  <div class="foot-rule"></div>
  <div class="pay"><span>Kardo</span><span>Merix</span><span>Paywell</span><span>Amvero</span></div>
  <div class="copy">Copyright © 2025 Velquint® | All Rights Reserved</div>
  <div class="social"><i></i><i></i><i></i></div>
</footer>

</body>
</html>
```